Business Card Design Project

We are not a new company, but renamed to "Vantorin Kitchens" last year. We specialize in modern high-end cabinetry imports. We would like to communicate a sense of quality and cutting edge technology. Ideally the design would incorporate our logo colors, silver, red and preferably a black, matte background. Though we are open to suggestions.
Logo is attached.
Edit: I have attached rough drafts of the previous cards, this way you will have all necessary content that needs to go on the cards.
Updates
Project Deadline Extended
Reason: We have received a lot of great designs, but due to the sheer number we couldn't respond to all. We will extend the deadline for another 7 days to finalize and provide feedback to designers.
Thank you for your hard work!
Industry/Entity Type
Business
Look and feel
Each slider illustrates characteristics of the customer's brand and the style your logo design should communicate.

```html
<!DOCTYPE html>
<html lang="en">
<head>
<meta charset="utf-8">
<title>Vantorin Kitchens – Business Cards</title>
<link href="https://fonts.googleapis.com/css2?family=Michroma&family=Questrial&display=swap" rel="stylesheet">
<style>
  :root {
    --stage: #d8cec3;
    --label: #2a2420;
    --card-dark: #1a1b1d;
    --card-mid: #2a2b2e;
    --card-black: #050505;
    --silver: #c8c9cc;
    --silver-light: #e9eaec;
    --silver-dark: #8d8f93;
    --text-light: #eceded;
    --red: #d9161c;
    --band-text: #ffffff;
  }
  * { box-sizing: border-box; margin: 0; padding: 0; }
  html, body { width: 1200px; height: 788px; overflow: hidden; }
  body {
    position: relative;
    background: var(--stage);
    font-family: "Questrial", sans-serif;
  }
  .label {
    position: absolute;
    width: 525px;
    text-align: center;
    font-family: "Questrial", sans-serif;
    font-size: 21px;
    color: var(--label);
  }
  .card {
    position: absolute;
    width: 525px;
    height: 300px;
    border-radius: 22px;
    overflow: hidden;
    background: radial-gradient(ellipse at 50% 35%, var(--card-mid) 0%, var(--card-dark) 70%);
    box-shadow: 0 6px 14px rgba(0,0,0,0.35);
  }
  .card--black { background: var(--card-black); }

  .brand {
    position: absolute;
    left: 0; right: 0;
    display: flex;
    align-items: center;
    justify-content: center;
    gap: 12px;
  }
  .brand__square {
    width: 18px; height: 18px;
    background: var(--silver);
  }
  .brand__name {
    font-family: "Michroma", sans-serif;
    font-size: 22px;
    letter-spacing: 1px;
    color: var(--silver);
    white-space: nowrap;
  }
  .card--front .brand { top: 92px; }
  .card--back .brand { top: 134px; }
  .card--back .brand__name { font-size: 25px; }

  .contact {
    position: absolute;
    left: 66px;
    top: 155px;
    list-style: none;
    font-size: 12.5px;
    letter-spacing: 1.2px;
    color: var(--text-light);
  }
  .contact li { display: flex; align-items: center; height: 20px; }
  .contact svg { width: 11px; height: 11px; margin-right: 9px; fill: var(--silver-dark); }
  .contact .email { font-size: 11px; letter-spacing: 0.8px; }

  .address {
    position: absolute;
    left: 346px;
    top: 181px;
    font-style: normal;
    font-size: 12px;
    letter-spacing: 1.4px;
    line-height: 17.5px;
    color: var(--text-light);
  }
  .address .small-caps { font-variant: small-caps; }

  .band { position: absolute; left: 0; top: 0; width: 525px; height: 300px; }
  .band__name {
    position: absolute;
    left: 0; right: 0;
    top: 269px;
    text-align: center;
    font-family: "Michroma", sans-serif;
    font-size: 13px;
    letter-spacing: 2px;
    color: var(--band-text);
  }
  .band__title { font-family: "Questrial", sans-serif; font-size: 10px; letter-spacing: 0.8px; text-transform: uppercase; }

  .texture {
    position: absolute;
    width: 260px;
    height: 80px;
  }
  .texture--top {
    left: 0; top: 0;
    background: radial-gradient(ellipse at 45% 30%, rgba(150,150,150,0.45) 0%, rgba(60,60,60,0.25) 45%, transparent 75%);
  }
  .texture--bottom {
    right: 0; bottom: 0;
    background: radial-gradient(ellipse at 55% 70%, rgba(150,150,150,0.45) 0%, rgba(60,60,60,0.25) 45%, transparent 75%);
  }
</style>
</head>
<body>

  <div class="label" style="left:53px; top:22px;">front</div>
  <div class="label" style="left:625px; top:22px;">front-1</div>
  <div class="label" style="left:55px; top:405px;">back</div>
  <div class="label" style="left:625px; top:405px;">Back - 1</div>

  <!-- Front: President -->
  <section class="card card--front" style="left:53px; top:63px;">
    <div class="brand"><span class="brand__square"></span><span class="brand__name">Vantorin Kitchens</span></div>
    <ul class="contact">
      <li><svg viewBox="0 0 12 12"><path d="M2 1h3l1 3-2 1a7 7 0 0 0 3 3l1-2 3 1v3a1 1 0 0 1-1 1A10 10 0 0 1 1 2a1 1 0 0 1 1-1z"/></svg>780.555.0142</li>
      <li><svg viewBox="0 0 12 12"><path d="M3 1h6v3H3zM1 5h10v5H9v1H3v-1H1zM4 8h4v2H4z"/></svg>780.555.0187</li>
      <li><svg viewBox="0 0 12 12"><path d="M3.5 0h5a1 1 0 0 1 1 1v10a1 1 0 0 1-1 1h-5a1 1 0 0 1-1-1V1a1 1 0 0 1 1-1zm0 2v7h5V2z"/></svg>780.555.0163</li>
      <li class="email"><svg viewBox="0 0 12 12"><path d="M0 3h12v7H0zm1 1v.5l5 3 5-3V4z"/></svg>marek@vantorinkitchens.ca</li>
    </ul>
    <address class="address">4812 - 87 <span class="small-caps">St.</span><br><span class="small-caps">Edmonton</span><br>AB T6X 2K4</address>
    <svg class="band" viewBox="0 0 525 300" aria-hidden="true">
      <defs>
        <linearGradient id="silverA" x1="0" y1="0" x2="1" y2="0">
          <stop offset="0" stop-color="#9a9b9f"/><stop offset="0.5" stop-color="#dcdde0"/><stop offset="1" stop-color="#f2f2f3"/>
        </linearGradient>
      </defs>
      <path d="M0 270 Q262 240 525 262 L525 300 L0 300 Z" fill="url(#silverA)"/>
      <path d="M0 268 Q262 238 525 260" fill="none" stroke="#d9161c" stroke-width="3"/>
      <path d="M0 263 Q262 233 525 255" fill="none" stroke="#d9161c" stroke-width="1.2" opacity="0.8"/>
    </svg>
    <div class="band__name">MAREK DOLAN, <span class="band__title">President</span></div>
  </section>

  <!-- Front-1: Director -->
  <section class="card card--front" style="left:625px; top:63px;">
    <div class="brand"><span class="brand__square"></span><span class="brand__name">Vantorin Kitchens</span></div>
    <ul class="contact" style="top:152px;">
      <li><svg viewBox="0 0 12 12"><path d="M2 1h3l1 3-2 1a7 7 0 0 0 3 3l1-2 3 1v3a1 1 0 0 1-1 1A10 10 0 0 1 1 2a1 1 0 0 1 1-1z"/></svg>780.555.0142</li>
      <li><svg viewBox="0 0 12 12"><path d="M3 1h6v3H3zM1 5h10v5H9v1H3v-1H1zM4 8h4v2H4z"/></svg>780.555.0187</li>
      <li><svg viewBox="0 0 12 12"><path d="M3.5 0h5a1 1 0 0 1 1 1v10a1 1 0 0 1-1 1h-5a1 1 0 0 1-1-1V1a1 1 0 0 1 1-1zm0 2v7h5V2z"/></svg>780.555.0129</li>
      <li class="email"><svg viewBox="0 0 12 12"><path d="M0 3h12v7H0zm1 1v.5l5 3 5-3V4z"/></svg>tomas@vantorinkitchens.ca</li>
    </ul>
    <address class="address" style="left:368px; top:177px;">4812 - 87 <span class="small-caps">St.</span><br><span class="small-caps">Edmonton</span><br>AB T6X 2K4</address>
    <svg class="band" viewBox="0 0 525 300" aria-hidden="true">
      <defs>
        <linearGradient id="silverB" x1="0" y1="0" x2="1" y2="0">
          <stop offset="0" stop-color="#9a9b9f"/><stop offset="0.5" stop-color="#dcdde0"/><stop offset="1" stop-color="#f2f2f3"/>
        </linearGradient>
      </defs>
      <path d="M0 270 Q262 240 525 262 L525 300 L0 300 Z" fill="url(#silverB)"/>
      <path d="M0 268 Q262 238 525 260" fill="none" stroke="#d9161c" stroke-width="3"/>
      <path d="M0 263 Q262 233 525 255" fill="none" stroke="#d9161c" stroke-width="1.2" opacity="0.8"/>
    </svg>
    <div class="band__name">TOMAS DOLAN, <span class="band__title">Director</span></div>
  </section>

  <!-- Back -->
  <section class="card card--back" style="left:55px; top:447px;">
    <div class="brand"><span class="brand__square"></span><span class="brand__name">Vantorin Kitchens</span></div>
  </section>

  <!-- Back-1 -->
  <section class="card card--back card--black" style="left:625px; top:447px;">
    <div class="texture texture--top" role="img" aria-label="Perforated metal texture, top left corner"></div>
    <div class="texture texture--bottom" role="img" aria-label="Perforated metal texture, bottom right corner"></div>
    <div class="brand"><span class="brand__square"></span><span class="brand__name">Vantorin Kitchens</span></div>
  </section>

</body>
</html>
```